Business card design for Virtual Assistance company

I need a business card designed for my virtual assistance company. We are a small company who services primarily C-level executive clients. The card needs to be double sided with the following contact information on the back:
Melissa Thornbury
Owner/CEO
info@rkpadvisory.net
www.rkpadvisory.net
555.302.9817

The front side should just have the company name incorporated: "RKP Advisory" and "virtual assistance"

The card should be simplistic, but eye catching and should speak to high level executives. Our primary focus areas consist of executive assistance and government contracting.

Target Market(s)

CEOs and executives

Contact Information for Business Card

see project description. phone, email, website.

Colors

Designer to choose only greyscale colors for use in the design.

```html
<!DOCTYPE html>
<html lang="en">
<head>
<meta charset="utf-8">
<title>RKP Advisory — Business Card</title>
<link rel="stylesheet" href="https://fonts.googleapis.com/css2?family=Libre+Baskerville:wght@400;700&family=Lato:wght@400&family=Poppins:wght@300&display=swap">
<style>
  :root {
    --backdrop: #2a2b2e;
    --card-white: #ffffff;
    --card-black: #202123;
    --ink: #1d1d1f;
    --ink-soft: #6f6f72;
    --rule-grey: #bdbdbd;
    --paper-text: #f2f2f2;
  }
  * { margin: 0; padding: 0; box-sizing: border-box; }
  html, body {
    width: 1200px; height: 952px; overflow: hidden;
    background: var(--backdrop);
  }
  .stage {
    width: 1200px; height: 952px;
    display: flex; align-items: center; justify-content: center; gap: 48px;
  }
  .card {
    position: relative;
    width: 540px; height: 309px;
    box-shadow: 0 12px 30px rgba(0,0,0,.45);
  }

  /* Contact side */
  .card--contact { background: var(--card-white); color: var(--ink); }
  .brand {
    position: absolute; top: 48px; left: 0; width: 100%;
    text-align: center;
    font-family: "Libre Baskerville", serif; font-weight: 400;
    font-size: 30px; letter-spacing: 2px; color: var(--ink);
  }
  .person {
    position: absolute; left: 44px; top: 150px;
  }
  .person__name {
    font-family: "Libre Baskerville", serif; font-weight: 700;
    font-size: 15px; letter-spacing: .5px; text-transform: uppercase;
  }
  .person__title {
    margin-top: 6px; text-align: right;
    font-family: "Lato", sans-serif; font-size: 13px; color: var(--ink-soft);
  }
  .contacts {
    position: absolute; left: 262px; top: 146px;
    list-style: none;
    font-family: "Lato", sans-serif; font-size: 13px; color: var(--ink-soft);
  }
  .contacts li { display: flex; align-items: center; gap: 7px; height: 24px; }
  .contacts svg { width: 16px; height: 16px; flex: none; }
  .card-rule { position: absolute; left: 0; bottom: 38px; width: 100%; height: 8px; }

  /* Brand side */
  .card--brand { background: var(--card-black); color: var(--paper-text); }
  .brand-block {
    position: absolute; inset: 0;
    display: flex; flex-direction: column; align-items: center; justify-content: center;
  }
  .brand-block__name {
    font-family: "Libre Baskerville", serif; font-weight: 400;
    font-size: 32px; letter-spacing: 2px;
  }
  .brand-block__tag {
    margin-top: 6px;
    font-family: "Poppins", sans-serif; font-weight: 300;
    font-size: 14px; letter-spacing: 1px;
  }
</style>
</head>
<body>
<main class="stage">
  <section class="card card--contact" aria-label="Card back with contact details">
    <h1 class="brand">RKP Advisory</h1>
    <div class="person">
      <p class="person__name">Melissa Thornbury</p>
      <p class="person__title">Owner/CEO</p>
    </div>
    <ul class="contacts">
      <li>
        <svg viewBox="0 0 16 16" aria-hidden="true"><rect width="16" height="16" rx="2" fill="#1d1d1f"/><path d="M5 3.5c.6 0 1.4 1.6 1.4 2.1 0 .5-.8.8-.8 1.2.3 1.1 1.4 2.3 2.5 2.6.4 0 .7-.8 1.2-.8s2.1.8 2.1 1.4c0 .8-1 1.6-1.9 1.6C6.6 11.6 4.4 9.4 3.4 6.5 3.4 4.5 4.3 3.5 5 3.5z" fill="#fff"/></svg>
        <span>555.302.9817</span>
      </li>
      <li>
        <svg viewBox="0 0 16 16" aria-hidden="true"><rect width="16" height="16" rx="2" fill="#1d1d1f"/><rect x="3" y="4.5" width="10" height="7" fill="none" stroke="#fff" stroke-width="1.2"/><path d="M3 4.5l5 4 5-4M3 11.5l3.8-3.6M13 11.5L9.2 7.9" fill="none" stroke="#fff" stroke-width="1.1"/></svg>
        <span>info@rkpadvisory.net</span>
      </li>
      <li>
        <svg viewBox="0 0 16 16" aria-hidden="true"><rect width="16" height="16" rx="2" fill="#1d1d1f"/><path d="M5 3l6.5 6-3 .3 1.7 3.3-1.2.6-1.7-3.3L5 12z" fill="#fff"/></svg>
        <span>www.rkpadvisory.net</span>
      </li>
    </ul>
    <svg class="card-rule" viewBox="0 0 540 8" preserveAspectRatio="none" aria-hidden="true">
      <rect x="0" y="3" width="232" height="3" fill="var(--rule-grey)"/>
      <polygon points="232,1 540,1 540,8 240,8" fill="var(--ink)"/>
    </svg>
  </section>

  <section class="card card--brand" aria-label="Card front with company name">
    <div class="brand-block">
      <p class="brand-block__name">RKP Advisory</p>
      <p class="brand-block__tag">virtual assistance</p>
    </div>
  </section>
</main>
</body>
</html>
```